Quillmarsh Property Solutions need a business card design

Hello guys. We would need a business card design asap please.
We are a start up property investment business based in London UK specialised in buying, selling, managing and letting properties and helping distressed property owners.
The name of our Business is Quillmarsh, the logo symbolises the four fundamental elements of the world (earth, air, fire and water) and so it stands for strength, stability, longevity.
We would like the business card to communicate professionalism and reliability. Many many thanks indeed for your work.

Details:

1.) Rosalind Updike
Property Investor
Mobile: +44(0)7700123456
Email: rosalind.quillmarsh@mailbox-example.com

2.) Dominic Updike
Property Investor
Mobile: +44(0)7700987654
Email: dominic.quillmarsh@mailbox-example.com

```html
<!DOCTYPE html>
<html lang="en">
<head>
<meta charset="utf-8">
<title>Quillmarsh Property Solutions – Business Card</title>
<link rel="stylesheet" href="https://fonts.googleapis.com/css2?family=Open+Sans:wght@400;600;700;800&display=swap">
<style>
  :root {
    --brand-blue: #2b52a3;
    --brand-blue-faint: #3a62b4;
    --card-white: #ffffff;
    --ink-dark: #1a1a1a;
    --ink-light: #ffffff;
    --ink-soft: #dfe7f7;
    --stage: #e9eaec;
    --card-shadow: 0 6px 18px rgba(0, 0, 0, 0.18);
  }
  * { box-sizing: border-box; margin: 0; padding: 0; }
  html, body {
    width: 1200px;
    height: 720px;
    overflow: hidden;
    background: var(--stage);
    font-family: "Open Sans", Arial, sans-serif;
  }
  .canvas {
    width: 1200px;
    height: 720px;
    display: flex;
    align-items: center;
    justify-content: center;
    gap: 60px;
  }
  .card {
    position: relative;
    width: 520px;
    height: 300px;
    overflow: hidden;
    box-shadow: var(--card-shadow);
  }

  /* Front */
  .card--front { background: var(--brand-blue); }
  .card-front__top {
    position: absolute;
    inset: 0 0 auto 0;
    height: 168px;
    background: var(--card-white);
  }
  .brand-lockup {
    position: absolute;
    left: 0;
    right: 0;
    top: 58px;
    text-align: center;
    color: var(--ink-dark);
  }
  .brand-lockup__name {
    font-weight: 800;
    font-size: 26px;
    letter-spacing: 0.06em;
    line-height: 1;
  }
  .brand-lockup__tagline {
    margin-top: 6px;
    font-weight: 700;
    font-size: 9px;
    letter-spacing: 0.16em;
  }
  .brand-mark-faint {
    position: absolute;
    right: 46px;
    top: 132px;
    font-weight: 800;
    font-size: 22px;
    letter-spacing: 0.06em;
    color: var(--brand-blue-faint);
  }
  .contact {
    position: absolute;
    left: 28px;
    bottom: 24px;
    color: var(--ink-light);
  }
  .contact__name {
    font-weight: 700;
    font-size: 18px;
    line-height: 1.1;
  }
  .contact__role {
    font-size: 12px;
    color: var(--ink-soft);
    margin-bottom: 10px;
  }
  .contact__line {
    display: flex;
    align-items: center;
    gap: 8px;
    font-size: 12.5px;
    line-height: 1.9;
  }
  .contact__icon { width: 12px; height: 12px; flex: none; }

  /* Back */
  .card--back {
    background: var(--brand-blue);
    display: flex;
    align-items: center;
    justify-content: center;
  }
  .brand-back {
    display: flex;
    align-items: center;
    gap: 14px;
    color: var(--ink-light);
    font-weight: 800;
    font-size: 38px;
    letter-spacing: 0.06em;
  }
  .brand-back__dot {
    width: 22px;
    height: 22px;
    border-radius: 50%;
    background: var(--ink-light);
  }
</style>
</head>
<body>
  <main class="canvas">
    <section class="card card--front" aria-label="Business card front">
      <div class="card-front__top"></div>
      <div class="brand-lockup">
        <div class="brand-lockup__name">QUILLMARSH</div>
        <div class="brand-lockup__tagline">PROPERTY SOLUTIONS</div>
      </div>
      <div class="brand-mark-faint" aria-hidden="true">QUILLMARSH</div>
      <div class="contact">
        <div class="contact__name">Dominic Updike</div>
        <div class="contact__role">Property Investor</div>
        <div class="contact__line">
          <svg class="contact__icon" viewBox="0 0 12 12" aria-hidden="true">
            <rect x="3" y="0.5" width="6" height="11" rx="1" fill="none" stroke="#fff" stroke-width="1.2"/>
            <rect x="4.3" y="2" width="3.4" height="5" fill="#fff"/>
            <circle cx="6" cy="9.3" r="0.7" fill="#fff"/>
          </svg>
          <span>+44(0)7700987654</span>
        </div>
        <div class="contact__line">
          <svg class="contact__icon" viewBox="0 0 12 12" aria-hidden="true">
            <rect x="0.6" y="2.2" width="10.8" height="7.6" rx="1" fill="none" stroke="#fff" stroke-width="1.2"/>
            <path d="M1 3 L6 7 L11 3" fill="none" stroke="#fff" stroke-width="1.2"/>
          </svg>
          <span>dominic.quillmarsh@mailbox-example.com</span>
        </div>
      </div>
    </section>

    <section class="card card--back" aria-label="Business card back">
      <div class="brand-back">
        <span class="brand-back__dot" aria-hidden="true"></span>
        <span>QUILLMARSH</span>
      </div>
    </section>
  </main>
</body>
</html>
```